We need professional looking business cards for our e-assessment business based in Europe. Our company is called Velmo.

You can just use sample name and addresses.

The colours we use are:

#70abe4 (blue)
#FF6600 (orange)

The back side should say: Online testing made simple

This is the print-shop we are using. Please look at the link for info about formats: http://nl.prindavo.com/help/faq/using-my-own-artwork.html

Target market is education and large corporations

Business

```html
<!DOCTYPE html>
<html lang="en">
<head>
<meta charset="utf-8">
<title>Velmo business cards</title>
<link rel="stylesheet" href="https://fonts.googleapis.com/css2?family=Questrial&display=swap">
<style>
  :root {
    --orange: #f26522;
    --blue: #70abe4;
    --ink: #3a3a3a;
    --grey-text: #555555;
    --card: #ffffff;
    --card-back-top: #ffffff;
    --card-back-bottom: #e4e4e4;
    --backdrop: #d9d8d4;
  }
  * { margin: 0; padding: 0; box-sizing: border-box; }
  html, body {
    width: 1200px;
    height: 871px;
    overflow: hidden;
    background: var(--backdrop);
    font-family: "Questrial", "Century Gothic", sans-serif;
  }
  .stage {
    position: relative;
    width: 1200px;
    height: 871px;
  }
  .card {
    position: absolute;
    width: 520px;
    height: 297px;
    box-shadow: 0 6px 18px rgba(0, 0, 0, 0.25);
  }
  .card--back {
    left: 80px;
    top: 120px;
    background: linear-gradient(160deg, var(--card-back-top) 0%, var(--card-back-bottom) 100%);
  }
  .back-mark {
    position: absolute;
    left: 200px;
    top: 58px;
    width: 120px;
    height: 120px;
    border-radius: 50%;
    background: var(--orange);
  }
  .back-tagline {
    position: absolute;
    left: 0;
    right: 0;
    top: 206px;
    text-align: center;
    color: var(--blue);
    font-size: 17px;
    letter-spacing: 1.5px;
    white-space: nowrap;
  }
  .card--front {
    left: 600px;
    top: 450px;
    background: var(--card);
  }
  .brand {
    position: absolute;
    left: 30px;
    top: 178px;
    display: flex;
    align-items: center;
    gap: 16px;
  }
  .brand-dot {
    width: 58px;
    height: 58px;
    border-radius: 50%;
    background: var(--orange);
  }
  .brand-name {
    color: var(--ink);
    font-size: 66px;
    line-height: 1;
    letter-spacing: 1px;
  }
  .contact {
    position: absolute;
    left: 318px;
    top: 176px;
    color: var(--grey-text);
    font-size: 12px;
    line-height: 1.75;
    letter-spacing: 0.6px;
    white-space: nowrap;
  }
  .contact-name {
    color: var(--ink);
    font-size: 17px;
    letter-spacing: 2.5px;
    margin-bottom: 4px;
  }
  .contact-company {
    color: var(--orange);
  }
</style>
</head>
<body>
  <main class="stage">
    <section class="card card--back" aria-label="Card back">
      <div class="back-mark"></div>
      <p class="back-tagline">Online testing made simple</p>
    </section>

    <section class="card card--front" aria-label="Card front">
      <div class="brand">
        <span class="brand-dot"></span>
        <span class="brand-name">velmo</span>
      </div>
      <div class="contact">
        <p class="contact-name">Lena M Vos</p>
        <p class="contact-company">velmo inc</p>
        <p>18 Wren Street, Halden</p>
        <p>QLD 4120</p>
      </div>
    </section>
  </main>
</body>
</html>
```